I need a business card designed using the logo provided either vertical or horizontal......Harbourline Property Group is an Australian based real estate company that caters for the upper end of the market so the design of the business card "must reflect" the companies image!!
Colour combinations are optional but "must be realistic" and must be able to be accurately useable CMYK colours.
Please consider that any colours used "must be able to be used" and be suitable in following designs for "pull out banner signs" and "real estate signs".
The colours and the font in the attached designs are for example and other combinations are encouraged.
Target Market(s)
The High End of the Australian real estate market
Industry/Entity Type
Business
Contact Information for Business Card
Logo - Business Name - Director + Licensed Real Estate Agent - Mobile Number (Cell Phone) - Business Number - Fax - Email Address - Web address
Requirements
Must have
- Designs and colours (CMYK) that can easily be interpreted by an Australian printer.
Nice to have
- Some alternative ideas on colour and font..........the ones provided are ok and have been provided as an example but I am looking for alternative ideas
Should not have
- Loud, overly bright colours. Designs that do not reflect the professional standards of the business.
- Designs that look good on a computer monitor but can not be re-created on a printing press.............this is most important when it comes to shading etc.

```html
<!DOCTYPE html>
<html lang="en">
<head>
<meta charset="utf-8">
<title>Harbourline Property Group – Business Card</title>
<link rel="stylesheet" href="https://fonts.googleapis.com/css2?family=Open+Sans:wght@400;600&display=swap">
<style>
  :root {
    --backdrop: #2f2a27;
    --card-black: #111111;
    --card-charcoal: #262626;
    --gold: #c48a24;
    --cream: #e6d3a3;
    --text-gold: #d19a35;
    --text-light: #e9e4d8;
    --text-silver: #c9ccd3;
  }
  * { box-sizing: border-box; margin: 0; padding: 0; }
  html, body {
    width: 1200px; height: 844px; overflow: hidden;
    background: var(--backdrop);
    font-family: "Open Sans", Arial, sans-serif;
  }
  .stage {
    position: relative; width: 1200px; height: 844px;
    display: flex; align-items: center; justify-content: center; gap: 60px;
  }
  .card {
    position: relative; width: 520px; height: 297px; overflow: hidden;
    background: linear-gradient(120deg, var(--card-black) 0%, var(--card-charcoal) 70%, var(--card-black) 100%);
    box-shadow: 0 6px 18px rgba(0,0,0,0.45);
  }

  /* Front side */
  .band { position: absolute; left: 0; width: 100%; }
  .band--top-gold { top: 0; height: 18px; background: var(--gold); }
  .band--top-cream { top: 22px; height: 5px; background: var(--cream); }
  .band--bottom-cream { bottom: 22px; height: 5px; background: var(--cream); }
  .band--bottom-gold { bottom: 0; height: 18px; background: var(--gold); }

  .brand {
    position: absolute; left: 30px; top: 112px; width: 210px;
    display: flex; align-items: center; gap: 10px;
  }
  .brand__mark { width: 14px; height: 14px; background: var(--gold); flex: none; }
  .brand__name {
    color: var(--text-silver); font-weight: 600; font-size: 17px;
    letter-spacing: 2px; line-height: 1.35; text-transform: uppercase;
  }

  .contact { position: absolute; left: 285px; top: 58px; width: 215px; }
  .contact__name {
    color: var(--text-gold); font-size: 16px; font-weight: 400; letter-spacing: 0.5px;
    padding-bottom: 3px; border-bottom: 1px solid var(--text-gold);
  }
  .contact__role { color: var(--text-light); font-size: 12.5px; margin-top: 3px; }
  .contact__address { color: var(--text-light); font-size: 11.5px; line-height: 1.4; margin-top: 14px; }
  .contact__list { list-style: none; margin-top: 14px; }
  .contact__item {
    display: flex; align-items: center; gap: 9px;
    color: var(--text-light); font-size: 12px; line-height: 1; margin-bottom: 7px;
  }
  .icon {
    width: 15px; height: 15px; background: var(--gold); flex: none;
    display: flex; align-items: center; justify-content: center;
  }
  .icon svg { width: 11px; height: 11px; }

  /* Back side */
  .card--back { background: radial-gradient(circle at 50% 42%, #2a2a2a 0%, var(--card-black) 65%); }
  .tab { position: absolute; width: 22px; height: 52px; background: var(--gold); }
  .tab::after { content: ""; position: absolute; top: 0; width: 5px; height: 100%; background: var(--cream); }
  .tab--left { left: 0; top: 150px; }
  .tab--left::after { right: 4px; }
  .tab--right { right: 0; top: 22px; }
  .tab--right::after { left: 4px; }
  .back-brand {
    position: absolute; inset: 0;
    display: flex; flex-direction: column; align-items: center; justify-content: center; gap: 14px;
  }
  .back-brand__mark { width: 18px; height: 18px; background: var(--gold); }
  .back-brand__name {
    color: var(--text-light); font-weight: 600; font-size: 21px;
    letter-spacing: 3px; text-transform: uppercase; text-align: center; line-height: 1.35;
  }
</style>
</head>
<body>
<main class="stage">
  <section class="card card--front" aria-label="Business card front">
    <div class="band band--top-gold"></div>
    <div class="band band--top-cream"></div>
    <div class="band band--bottom-cream"></div>
    <div class="band band--bottom-gold"></div>

    <div class="brand">
      <span class="brand__mark"></span>
      <span class="brand__name">Harbourline<br>Property Group</span>
    </div>

    <div class="contact">
      <h1 class="contact__name">MARCUS ELLERY</h1>
      <p class="contact__role">Managing Director</p>
      <p class="contact__address">88 Quayside Parade<br>Sydney, NSW | 2000</p>
      <ul class="contact__list">
        <li class="contact__item">
          <span class="icon"><svg viewBox="0 0 12 12"><path d="M2 2h2l1 2.5-1.2.8a6 6 0 0 0 2.9 2.9l.8-1.2L10 8v2a1 1 0 0 1-1 1A8 8 0 0 1 1 3a1 1 0 0 1 1-1z" fill="#111"/></svg></span>
          (044)-318-2604
        </li>
        <li class="contact__item">
          <span class="icon"><svg viewBox="0 0 12 12"><rect x="3.5" y="1" width="5" height="10" rx="1" fill="#111"/><rect x="4.5" y="2.5" width="3" height="6" fill="#c48a24"/></svg></span>
          123-582-9047
        </li>
        <li class="contact__item">
          <span class="icon"><svg viewBox="0 0 12 12"><rect x="1" y="3" width="10" height="6.5" fill="#111"/><path d="M1 3l5 3.5L11 3" stroke="#c48a24" stroke-width="1" fill="none"/></svg></span>
          hello@harbourline.com.au
        </li>
        <li class="contact__item">
          <span class="icon"><svg viewBox="0 0 12 12"><path d="M5 7l2-2M4.2 5.5 3 6.7a1.6 1.6 0 0 0 2.3 2.3l1.2-1.2M7.8 6.5 9 5.3A1.6 1.6 0 0 0 6.7 3L5.5 4.2" stroke="#111" stroke-width="1.3" fill="none" stroke-linecap="round"/></svg></span>
          www.harbourlinegroup.com
        </li>
      </ul>
    </div>
  </section>

  <section class="card card--back" aria-label="Business card back">
    <div class="tab tab--left"></div>
    <div class="tab tab--right"></div>
    <div class="back-brand">
      <span class="back-brand__mark"></span>
      <span class="back-brand__name">Harbourline<br>Property Group</span>
    </div>
  </section>
</main>
</body>
</html>
```